Business card design for my company.
I would like the card's background colour to be black. You can also see our web site to get an idea of our brand. https://www.tmwhomecrafting.com.au/
- Name
- Email

```html
<!DOCTYPE html>
<html lang="en">
<head>
<meta charset="utf-8">
<title>TMW Home Crafting — Business Card</title>
<link rel="stylesheet" href="https://fonts.googleapis.com/css2?family=Montserrat:wght@400;500;700;800&display=swap">
<style>
  :root {
    --stage: #1c1c1c;
    --card: #050505;
    --green: #14964a;
    --white: #f4f4f4;
    --muted: #d9d9d9;
  }
  * { box-sizing: border-box; margin: 0; padding: 0; }
  html, body { width: 1200px; height: 875px; overflow: hidden; background: var(--stage); }
  body { position: relative; font-family: "Montserrat", sans-serif; }

  .card {
    position: absolute;
    width: 525px;
    height: 300px;
    border-radius: 18px;
    background: var(--card);
    overflow: hidden;
    box-shadow: 0 18px 40px rgba(0,0,0,.55);
  }
  .card--front { left: 70px; top: 130px; }
  .card--back  { left: 605px; top: 445px; }

  .brand {
    position: absolute;
    display: flex;
    align-items: center;
    gap: 14px;
    color: var(--white);
    font-weight: 800;
    letter-spacing: 0.06em;
    text-transform: uppercase;
  }
  .brand__name { line-height: 1.1; }
  .brand__mark { background: var(--green); flex: none; }
  .card--front .brand { left: 50%; top: 50%; transform: translate(-50%, -50%); font-size: 34px; white-space: nowrap; }
  .card--front .brand__mark { width: 26px; height: 26px; }
  .card--back .brand { left: 40px; top: 112px; width: 200px; font-size: 21px; gap: 10px; }
  .card--back .brand__mark { width: 16px; height: 16px; }

  .divider {
    position: absolute;
    left: 268px; top: 70px;
    width: 1.5px; height: 112px;
    background: var(--green);
  }

  .contact { position: absolute; left: 288px; top: 62px; color: var(--muted); }
  .contact__name { font-size: 22px; font-weight: 800; color: var(--white); line-height: 1; }
  .contact__name .first { color: var(--green); }
  .contact__role { font-size: 11.5px; font-weight: 500; margin-top: 4px; }
  .contact__list { list-style: none; margin-top: 16px; }
  .contact__list li {
    display: flex; align-items: center; gap: 9px;
    font-size: 11.5px; line-height: 1; margin-bottom: 9px;
  }
  .contact__list svg { width: 11px; height: 11px; fill: var(--green); flex: none; }

  .bands { position: absolute; left: 0; bottom: 0; width: 525px; height: 300px; }
</style>
</head>
<body>

  <section class="card card--front" aria-label="Card front">
    <div class="brand"><span class="brand__mark"></span><span class="brand__name">TMW Home Crafting</span></div>
  </section>

  <section class="card card--back" aria-label="Card back">
    <svg class="bands" viewBox="0 0 525 300" aria-hidden="true">
      <polygon points="0,284 332,252 318,300 0,300" fill="var(--white)"/>
      <polygon points="348,250 525,212 525,300 334,300" fill="var(--green)"/>
    </svg>

    <div class="brand"><span class="brand__mark"></span><span class="brand__name">TMW Home<br>Crafting</span></div>

    <div class="divider"></div>

    <div class="contact">
      <p class="contact__name"><span class="first">John</span> Smith</p>
      <p class="contact__role">Managing Director</p>
      <ul class="contact__list">
        <li>
          <svg viewBox="0 0 24 24"><path d="M4 2h5l2 5-3 2a12 12 0 0 0 7 7l2-3 5 2v5c0 1-1 2-2 2A19 19 0 0 1 2 4c0-1 1-2 2-2z"/></svg>
          (08) 9000 4821
        </li>
        <li>
          <svg viewBox="0 0 24 24"><path d="M2 5h20v14H2zm2 2v.4l8 5.2 8-5.2V7zm0 2.8V17h16V9.8l-8 5.2z"/></svg>
          info@websitename.com
        </li>
        <li>
          <svg viewBox="0 0 24 24"><circle cx="12" cy="12" r="10"/></svg>
          www.emailname.com
        </li>
      </ul>
    </div>
  </section>

</body>
</html>
```